I just need to get that same logo on the business card but with different word. “The Hinges Roadside and Rental”

Name: Marek T
Number: 4759028416
Email: thehingesroadside@brivomail.test

On the back, can we di just the logo and the hinges roadside and rental around it.

If possible a black card with the gold storefront type font that you used before, would be amazing. I attached the original logo just in case.

Target Market(s)

Roadside assistance

Industry/Entity Type

Repair/ roadside

Contact Information for Business Card

Name, email, phone number

Requirements
Must have
• Everything in description
Nice to have
• Nice big logo

```html
<!DOCTYPE html>
<html lang="en">
<head>
<meta charset="utf-8">
<title>The Hinges Roadside and Rental – Business Card</title>
<link href="https://fonts.googleapis.com/css2?family=Montserrat:wght@300;400;600;700&display=swap" rel="stylesheet">
<style>
  :root {
    --backdrop: #141414;
    --card: #1c1c1d;
    --card-edge: #0c0c0c;
    --gold: #b48d4e;
    --gold-soft: #9c7a44;
  }
  * { box-sizing: border-box; margin: 0; padding: 0; }
  html, body {
    width: 1200px;
    height: 857px;
    overflow: hidden;
    background: var(--backdrop);
    font-family: "Montserrat", Arial, sans-serif;
  }
  .canvas {
    position: relative;
    width: 1200px;
    height: 857px;
  }
  .card {
    position: absolute;
    width: 600px;
    height: 343px;
    background: var(--card);
    border-radius: 4px;
    box-shadow: 0 18px 40px rgba(0,0,0,0.55), 0 0 0 1px var(--card-edge);
    color: var(--gold);
  }
  .card--front { left: 120px; top: 50px; }
  .card--back  { left: 480px; top: 464px; }

  /* Front */
  .brand {
    position: absolute;
    inset: 0;
    display: flex;
    flex-direction: column;
    align-items: center;
    justify-content: center;
    text-align: center;
  }
  .brand__square {
    width: 46px;
    height: 46px;
    background: var(--gold);
    margin-bottom: 26px;
  }
  .brand__name {
    font-weight: 600;
    font-size: 52px;
    letter-spacing: 3px;
    line-height: 1;
  }
  .brand__tagline {
    font-weight: 600;
    font-size: 17px;
    letter-spacing: 5px;
    margin-top: 12px;
  }

  /* Back */
  .holder {
    position: absolute;
    left: 58px;
    bottom: 68px;
    font-weight: 700;
    font-size: 34px;
    letter-spacing: 2px;
  }
  .contact {
    position: absolute;
    left: 270px;
    bottom: 72px;
    list-style: none;
    font-weight: 400;
    font-size: 15px;
    letter-spacing: 1px;
    color: var(--gold-soft);
  }
  .contact__item {
    display: flex;
    align-items: center;
    gap: 9px;
    margin-top: 12px;
  }
  .contact__icon { width: 14px; height: 14px; fill: var(--gold); flex: none; }
</style>
</head>
<body>
<div class="canvas">
  <section class="card card--front" aria-label="Card front">
    <div class="brand">
      <div class="brand__square"></div>
      <div class="brand__name">THE HINGES</div>
      <div class="brand__tagline">ROADSIDE AND RENTAL</div>
    </div>
  </section>

  <section class="card card--back" aria-label="Card back">
    <div class="holder">MAREK T</div>
    <ul class="contact">
      <li class="contact__item">
        <svg class="contact__icon" viewBox="0 0 24 24" aria-hidden="true"><path d="M6.6 10.8a15.1 15.1 0 0 0 6.6 6.6l2.2-2.2a1 1 0 0 1 1-.25 11.4 11.4 0 0 0 3.6.57 1 1 0 0 1 1 1V20a1 1 0 0 1-1 1A17 17 0 0 1 3 4a1 1 0 0 1 1-1h3.5a1 1 0 0 1 1 1c0 1.25.2 2.45.57 3.6a1 1 0 0 1-.25 1z"/></svg>
        <span>4759028416</span>
      </li>
      <li class="contact__item">
        <svg class="contact__icon" viewBox="0 0 24 24" aria-hidden="true"><path d="M2 5h20v14H2z M3 6l9 7 9-7" fill="none" stroke="currentColor"/><path d="M2 5h20v2l-10 7L2 7z"/><path d="M2 8.5l10 7 10-7V19H2z"/></svg>
        <span>thehingesroadside@brivomail.test</span>
      </li>
    </ul>
  </section>
</div>
</body>
</html>
```